Mobile Repair Service on location needs a Web Design

We are starting a new mobile device repair service called Handset Haven and our website needs a design!

Hello Designers!
First, we'd like to make clear this is more than a simple web design contest, we want the designers to create an idea. We want someone who can create the whole theme of the service's we provide. We want someone that can help design our visual branding, help us communicate a sentiment. And we are willing to pay for that.

Who are we?
Our company is based in Rotterdam, the Netherlands. We provide different services for all kinds of electronic devices. The kind of services we provide are, among other things, installations of hardware and software and the repair of broken or malfunctioning devices.
We are starting a new service that offers mobile device repairs on location, be it at the home of our customers, their office, or any other place. Just give us the address and we will come to you for the repair job. This is also our main USP. We have multiple skilled engineers who drive trough the country on a daily basis and can be on location within a working day. Repair is done immediately onsite while the customer waits. At this stage we will start with the smartphone product-group within the mobile devices. In a second phase we might also add tablets.
People don't want to be without their phone for weeks because of some parts that needed to be ordered by a repair center they had to sent their phone to. We offer a fully functional mobile repair center in the form of specially customized vans. These vans have all the tools and utilities needed by our engineers to safely repair your mobile device. Your phone is being repaired directly in front of you, the next business-day, on a location you desire.

For this new service we are creating a website called Handset Haven. The website needs a story and matching design and this is where you come in. We are not looking for a simple template design we can get from any place. We need a story. We want you to create an idea, build a unique theme or vision that helps sell the product/service. This goes beyond the design of the website. We need the whole package, the design you are creating needs to have returning elements like icons, color use, images, maybe even characters etc. You name it! There needs to be a common thread in the design so we can reuse elements in, for example, the email templates, the work order or receipt we give to our customers (we may contact the winner of the contest to design these for us as well!).

The name 'Handset Haven' is chosen. Rehab (short for rehabilitate) has a bold and playful tone to it and the design needs to reflect the name. So we're looking for a somewhat playful and cheeky design. Definitely not too serious and definitely modern. We already got a logo that we love and that fit's this description (see attached design documents for the logo). It's bold, powerful and fun. Our web design needs to reflect this as well and has to fit in with our logo.
We would really like it if the design somehow incorporates elements that highlight our unique selling points (repairs on location, we come to you etc.). We would really like some form of story telling in the design. Think clumsy people breaking their phones. Teenagers in tears because they have no access to their friends. People nowadays have the need to always be 'connected'. What happens when your phone is broken or malfunctioning? We're handling tech, we are nerds and a little bit weird, but we're professionals and here to help you with your problem. The sentiment Byte Brigade tries to communicate is something we really like. We're looking for fresh idea's, anything goes!

In an overview all Unique Selling Points of the Handset haven service:
- Professional service on location. Don’t ship to us we will come to you!
- Clear pricing upfront. No hidden cost.
- Next business-day repair.
- Backed by a professional call center open 12 hours a day and open on a Saturday as well
- Backed by a professional repair center with more then 12 years of experience
- Repair is done by certified engineers
- 1 year warranty on the repair

The process:
The main function of our website will be for customers to make a repair request. A customer will visit our website and can make a repair request immediately by going through a 'request-order-flow'. In this flow he or she will need to fill in some forms and can select wich type/model/brand of mobile device he or she has and what parts need to be repaired. After a request is placed we will call the customer back (within an hour) for a short intake and to set a date/time and location. Our engineer will meet the customer at the specified location and will repair the device onsite in one of our mobile repair centers, which is a specialized van equipped with all the tools needed for device restorations.
So in short the steps are:
- Choose your device and repair job
- Place the order
- Get a callback within the hour
- Set date and location
- We will come to you.

Website functionality:
Our website is our main form of communication. So the sentiment we want to communicate needs be reflected in the design. We need a main/front page designed (preferably a long scrolling page design) containing:
1. Customers will be able to request a repair job directly on our website. So there will need to be a prominent button/link at the top of our main page that will bring the customer to this 'request-order-flow'. This is the main flow which needs to be full focus on the front page. All other items are secondary.
2. The general information of who we are and what we do, and why the customer should choose us. Preferably in short bullet-point type keywords/sentences with icons or other visual cues. See our unique selling points to get an idea of the information that will be displayed here.
3. There needs to be a section that will explain the process (see above) of a repair request step-by- step, again in brief short key sentences and with (custom) icons.
4. There needs to be a section that explains to the customer he/she can always contact us if they are not sure what the problem is with their device, and for this reason are not sure what repair request they should order.
5. We want to implement some functionality that display customer ratings or customer reviews. So there needs to be room for some kind of widget of plugin we're going to implement which shows these reviews.
6. A 'For business section' where we will explain all the options we provide for corporate clients.
7. Social media links.
8. There needs to be a menu with buttons that leads to the all sections described in the previous points.

For now, we need a design for our front page. In the second phase, when we have picked our winner, we may ask the winner to design the page(s) for our request workflow as well.

EDIT:
Finally, we have a very specific order in mind for the different segments of our website. We would like you to add some more segments that were not in our original brief as well:

1. Top header with order/request button. (should instantly make clear our main USP, we do repairs on location)
2. Our process
3. Our unique selling points / why choose us
4. The kind of repairs we do (broken screens, broken batteries, water damage, broken camera's, no sound etc.)
5. A 'meet our team' section, where we introduce some of our engineers
6. A 'contact us for any questions' section/
7. Testimonials/user reviews
8. A section where we show key performance indicators
9. 'For businesses' sections
10.'Subscribe for newsletter' field
11. Social media buttons

Industry/Entity Type

It Service

Number of Pages Required

1 page

Font styles to use
Sans Serif

Requirements
Must have
• a main/front page, design only
• custom icons/images for banners, adverts online and in print (high res)
Nice to have
• Storytelling in our design.
• Design that fits with our brand new logo.
• Elements like icons to have a flat design.
• Keep in mind that the website will need to be responsive when designing! (Ideally provide an example of the mobile design as well)
• Create a fun and trustworthy feeling.

```html
<!DOCTYPE html>
<html lang="en">
<head>
<meta charset="utf-8">
<title>Handset Haven – Mobile Repair On Location</title>
<link href="https://fonts.googleapis.com/css2?family=Raleway:wght@300;400;500;600;700;800&display=swap" rel="stylesheet">
<style>
:root{
  --orange:#f0592a;
  --orange-dark:#e0461a;
  --orange-light:#ff8a4c;
  --ink:#1d1d1f;
  --grey:#6b6b6b;
  --line:#e3e3e3;
  --lavender:#dcdcee;
  --ring:#c9c6f0;
  --footer:#121a20;
  --white:#ffffff;
}
*{margin:0;padding:0;box-sizing:border-box}
html,body{width:1200px;height:3797px;overflow:hidden}
body{font-family:'Raleway',sans-serif;color:var(--ink);background:var(--white);position:relative}
.btn{display:inline-block;background:var(--orange);color:var(--white);font-size:14px;font-weight:500;border-radius:20px;padding:10px 34px;text-decoration:none}
.section-title{text-align:center;font-weight:400;font-size:30px;line-height:1.15}
.section-title strong{display:block;font-weight:700}
.section-title::after{content:"";display:block;width:44px;height:3px;background:var(--orange);margin:14px auto 0}

/* header */
.site-header{position:absolute;top:0;left:0;width:1200px;height:111px;display:flex;align-items:center;padding:0 80px;background:var(--white);z-index:2}
.brand{display:flex;align-items:center;gap:12px}
.brand-dot{width:58px;height:58px;border-radius:50%;background:var(--orange)}
.brand-name{font-weight:800;font-size:24px;line-height:1;color:var(--ink);width:130px}
.brand-tag{font-size:10px;color:var(--orange);font-weight:600;margin-top:4px}
.main-nav{margin-left:auto;display:flex;align-items:center;gap:20px;font-size:15px}
.main-nav a{color:var(--ink);text-decoration:none}
.main-nav a.active{color:var(--orange)}
.main-nav .btn{margin-left:10px;padding:10px 32px}

/* hero */
.hero{position:absolute;top:111px;left:0;width:1200px;height:600px;background:linear-gradient(90deg,#d9d6d3,#ebe8e4 45%,#c9b9a8);clip-path:polygon(0 0,100% 0,100% 88%,0 100%)}
.hero-photo{position:absolute;right:0;top:0;width:520px;height:100%;background:linear-gradient(160deg,#b89a7e,#8d6a50 60%,#3c4d6b)}
.hero-copy{position:absolute;left:80px;top:150px;width:640px}
.hero-copy h1{font-size:45px;line-height:1.35;font-weight:400;color:var(--orange)}
.hero-copy h1 span{display:block;color:var(--ink);font-weight:600}
.hero-copy p{font-size:15px;line-height:1.65;color:#3a3a3a;margin:28px 0 34px;width:640px}

/* intro columns */
.intro{position:absolute;top:730px;left:85px;width:1030px;display:flex}
.intro-col{flex:1;text-align:center;padding:0 35px;border-right:1px solid var(--line)}
.intro-col:last-child{border-right:none}
.intro-icon{height:54px;display:flex;justify-content:center;align-items:center}
.intro-col h2{font-size:27px;font-weight:400;line-height:1.2;margin-top:12px}
.intro-col h2 strong{display:block;font-weight:700}
.intro-col p{font-size:12.5px;line-height:2;color:var(--grey);margin:22px 0 28px;min-height:150px}

/* services */
.services{position:absolute;top:1190px;left:0;width:1200px;height:562px;background:radial-gradient(ellipse at 60% 40%,var(--orange-light),var(--orange) 55%,var(--orange-dark))}
.services .section-title{color:var(--white);margin-top:50px}
.services .section-title::after{background:var(--white)}
.usp-list{position:absolute;top:195px;left:75px;width:1050px;display:flex;justify-content:space-between}
.usp{width:140px;text-align:center;color:var(--white)}
.usp-badge{width:130px;height:130px;border-radius:50%;background:var(--ring);margin:0 auto;display:flex;align-items:center;justify-content:center}
.usp-badge span{width:94px;height:94px;border-radius:50%;background:#3b3f4a;display:flex;align-items:center;justify-content:center}
.usp-stem{width:0;height:42px;border-left:2px dotted rgba(255,255,255,.8);margin:0 auto}
.usp-dot{width:12px;height:12px;border-radius:50%;background:#3b3f4a;border:2px solid var(--white);margin:0 auto 18px}
.usp h3{font-size:14px;font-weight:700;line-height:1.35}
.usp p{font-size:12px;line-height:1.6}

/* process */
.process{position:absolute;top:1752px;left:0;width:1200px;height:572px}
.process .section-title{margin-top:58px}
.steps{position:absolute;top:205px;left:70px;width:1060px;display:flex;justify-content:space-between}
.step{width:190px;text-align:center}
.step-art{width:130px;height:170px;margin:0 auto 18px;border-radius:60px 60px 20px 20px;background:linear-gradient(180deg,#f3dcc6,#e9e9ee 45%,#3c3f48)}
.step h3{font-size:15px;font-weight:500;color:var(--orange);line-height:1.5}
.step p{font-size:12px;color:var(--grey);line-height:1.55;margin-top:14px}

/* help */
.help{position:absolute;top:2324px;left:0;width:1200px;height:461px;background:linear-gradient(90deg,#f6f2ed,#efe6dc 50%,#d8c4ae)}
.help-photo{position:absolute;right:0;top:0;width:520px;height:100%;background:linear-gradient(150deg,#e5d3bd,#b79378 50%,#6c88a6)}
.help-copy{position:absolute;left:80px;top:72px;width:640px}
.help-copy p{font-size:30px;line-height:1.45;color:var(--orange);font-weight:400}
.help-copy h2{font-size:30px;line-height:1.45;font-weight:700;margin:18px 0 34px}

/* testimonials */
.testimonials{position:absolute;top:2785px;left:0;width:1200px;height:400px}
.testimonials .section-title{margin-top:60px}
.reviews{position:absolute;top:200px;left:80px;width:1040px;display:flex;justify-content:space-between}
.review{width:500px;display:flex;gap:30px;align-items:flex-start}
.review-photo{flex:none;width:125px;height:125px;border-radius:50%;border:6px solid var(--orange);background:linear-gradient(160deg,#d4b9a3,#8a7564)}
.review blockquote{font-size:13px;line-height:1.8;color:var(--grey);position:relative;padding:14px 0 0 22px}
.review blockquote::before{content:"\201C";position:absolute;left:0;top:0;font-size:40px;color:var(--ink);font-weight:700;line-height:1}
.review cite{display:block;font-style:normal;color:var(--orange);margin-top:16px}

/* business */
.business{position:absolute;top:3185px;left:0;width:1200px;height:213px;background:var(--lavender);display:flex;align-items:center}
.business-label{width:300px;text-align:center;font-size:30px;font-weight:400;line-height:1.15;border-right:1px solid #b9b9d2}
.business-label strong{display:block;font-weight:700}
.business-body{padding-left:20px}
.business-body h2{font-size:30px;font-weight:400;color:#2b2b33}
.business-body ul{list-style:none;margin-top:16px}
.business-body li{color:var(--orange);font-weight:700;font-size:15px;line-height:1.75}
.business-body li::before{content:"\2022";margin-right:8px}

/* footer */
.site-footer{position:absolute;top:3398px;left:0;width:1200px;height:349px;background:var(--footer);color:var(--white);display:flex;gap:48px;padding:68px 80px 0}
.foot-col{flex:1}
.foot-col h4{font-size:18px;font-weight:400;color:var(--orange);padding-bottom:12px;border-bottom:1px solid #3a434a;margin-bottom:16px}
.foot-col ul{list-style:none;font-size:13px;line-height:1.7}
.quick li::before{content:"\203A";margin-right:8px}
.contact li{display:flex;gap:12px;align-items:flex-start;margin-bottom:10px}
.contact .hot{color:var(--orange);font-size:15px}
.newsletter p{font-size:13px;line-height:1.6;margin-bottom:14px}
.news-field{width:200px;height:26px;background:var(--white);color:#999;font-size:11px;padding:6px 8px;margin-bottom:12px}
.news-btn{display:inline-block;background:var(--orange);font-size:12px;padding:4px 12px}
.social li{display:flex;align-items:center;gap:12px;margin-bottom:14px}
.social i{width:22px;height:22px;background:var(--orange);display:block}
.copyright{position:absolute;top:3747px;left:0;width:1200px;height:50px;background:var(--orange);color:var(--white);font-size:12px;display:flex;align-items:center;justify-content:center}
</style>
</head>
<body>

<header class="site-header">
  <div class="brand">
    <span class="brand-dot"></span>
    <div>
      <div class="brand-name">Handset Haven</div>
      <div class="brand-tag">We will come to you!</div>
    </div>
  </div>
  <nav class="main-nav">
    <a class="active" href="#">Home</a><a href="#">Who We Are</a><a href="#">What We Do</a><a href="#">Our Process</a><a href="#">Pricing</a><a href="#">Testimonials</a><a href="#">Our Clients</a>
    <a class="btn" href="#">Contact Us</a>
  </nav>
</header>

<section class="hero">
  <div class="hero-photo" role="img" aria-label="Smiling young woman in a yellow sweater sitting on a city ledge using her smartphone"></div>
  <div class="hero-copy">
    <h1>Best Mobile Repair Service<span>At Any Time In Anywhere</span></h1>
    <p>We are starting a new service that offers mobile device repairs on location, be it at the home of our customers, their office, or any other place. Just give us the address and we will come to you for the repair job.</p>
    <a class="btn" href="#">Call Now</a>
  </div>
</section>

<section class="intro">
  <article class="intro-col">
    <div class="intro-icon"><svg width="54" height="48" viewBox="0 0 54 48"><g fill="#f0592a"><circle cx="27" cy="10" r="8"/><circle cx="10" cy="20" r="6"/><circle cx="44" cy="20" r="6"/><path d="M13 46c0-10 6-16 14-16s14 6 14 16z"/><path d="M0 46c0-8 4-12 10-12 3 0 5 1 6 2-3 3-4 6-4 10z"/><path d="M54 46c0-8-4-12-10-12-3 0-5 1-6 2 3 3 4 6 4 10z"/></g></svg></div>
    <h2>Who<strong>We Are</strong></h2>
    <p>Our company is based in Rotterdam, the Netherlands. We provide different services for all kinds of electronic devices. The kind of services we provide are, among other things, installations of hardware and software and the repair of broken or malfunctioning devices.</p>
    <a class="btn" href="#">Read More</a>
  </article>
  <article class="intro-col">
    <div class="intro-icon"><svg width="30" height="52" viewBox="0 0 30 52"><rect x="2" y="2" width="26" height="48" rx="4" fill="none" stroke="#2a2a2a" stroke-width="3"/><rect x="6" y="9" width="18" height="32" fill="#f0592a"/><circle cx="15" cy="45" r="2" fill="#2a2a2a"/></svg></div>
    <h2>What<strong>We Do</strong></h2>
    <p>We are starting a new service that offers mobile device repairs on location, be it at the home of our customers, their office, or any other place. Just give us the address and we will come to you for the repair job. We offer a fully functional mobile repair center in the form of specially customized vans.</p>
    <a class="btn" href="#">Read More</a>
  </article>
  <article class="intro-col">
    <div class="intro-icon"><svg width="40" height="52" viewBox="0 0 40 52"><path d="M14 4v26l-6-5-4 4 12 15h18l4-16-14-4V4z" fill="#2a2a2a"/><circle cx="17" cy="8" r="7" fill="#f0592a"/></svg></div>
    <h2>Why<strong>Choose Us</strong></h2>
    <p>We have multiple skilled engineers who drive trough the country on a daily basis and can be on location within a working day. Repair is done immediately onsite while the customer waits. Your phone is being repaired directly in front of you, the next business-day, on a location you desire.</p>
    <a class="btn" href="#">Read More</a>
  </article>
</section>

<section class="services">
  <h2 class="section-title">Our<strong>Services</strong></h2>
  <div class="usp-list">
    <div class="usp">
      <div class="usp-badge"><span><svg width="44" height="44" viewBox="0 0 44 44" fill="#fff"><circle cx="26" cy="7" r="5"/><path d="M18 14h10l4 10 6 2-1 3-8-3-3-5-3 8 6 6-2 9h-4l1-8-6-5-4 9-8-2 1-3 5 1 5-13-4 2-3 6-3-1 4-8z"/></svg></span></div>
      <div class="usp-stem"></div><div class="usp-dot"></div>
      <h3>Professional service <span style="font-weight:400">on location.</span></h3>
      <p>Don't ship to us we will come to you!</p>
    </div>
    <div class="usp">
      <div class="usp-badge"><span><svg width="44" height="44" viewBox="0 0 44 44" fill="#fff"><circle cx="26" cy="14" r="10"/><text x="26" y="19" font-size="14" text-anchor="middle" fill="#3b3f4a" font-family="Raleway,sans-serif" font-weight="700">$</text><path d="M2 30h10l8 4h10l8-4 3 3-10 8H14l-12-4z"/></svg></span></div>
      <div class="usp-stem"></div><div class="usp-dot"></div>
      <h3>Clear pricing upfront.</h3>
      <p>No hidden cost.</p>
    </div>
    <div class="usp">
      <div class="usp-badge"><span><svg width="44" height="44" viewBox="0 0 44 44"><circle cx="22" cy="22" r="19" fill="none" stroke="#fff" stroke-width="3"/><path d="M15 12l5 5-3 3c2 4 4 6 8 8l3-3 5 5-4 4c-9-1-17-9-18-18z" fill="#fff"/></svg></span></div>
      <div class="usp-stem"></div><div class="usp-dot"></div>
      <h3>Backed by a professional call center</h3>
      <p>open 12 hours a day and open on a Saturday as well.</p>
    </div>
    <div class="usp">
      <div class="usp-badge"><span><svg width="44" height="44" viewBox="0 0 44 44" fill="none" stroke="#fff" stroke-width="3"><rect x="5" y="8" width="34" height="30" rx="3"/><path d="M5 16h34M13 4v8M31 4v8"/><g fill="#fff" stroke="none"><rect x="11" y="21" width="5" height="4"/><rect x="19" y="21" width="5" height="4"/><rect x="27" y="21" width="5" height="4"/><rect x="11" y="29" width="5" height="4"/><rect x="19" y="29" width="5" height="4"/></g></svg></span></div>
      <div class="usp-stem"></div><div class="usp-dot"></div>
      <h3>Next business-day</h3>
      <p>repair.</p>
    </div>
    <div class="usp">
      <div class="usp-badge"><span><svg width="44" height="44" viewBox="0 0 44 44" fill="#fff"><path d="M8 34l20-20-2-6 6-4 4 4-4 6-6-2-20 20z"/><path d="M30 30l6 6-4 4-6-6zM6 10l4-4 18 18-4 4z"/></svg></span></div>
      <div class="usp-stem"></div><div class="usp-dot"></div>
      <h3>Backed by a professional repair center</h3>
      <p>with more then 12 years of experience come to you!</p>
    </div>
    <div class="usp">
      <div class="usp-badge"><span><svg width="44" height="44" viewBox="0 0 44 44" fill="#fff"><circle cx="14" cy="14" r="6"/><circle cx="30" cy="14" r="6"/><path d="M2 34c0-8 5-12 12-12s12 4 12 12z"/><path d="M18 34c0-8 5-12 12-12s12 4 12 12z"/></svg></span></div>
      <div class="usp-stem"></div><div class="usp-dot"></div>
      <h3>Repair is done by <span style="font-weight:400">certified engineers.</span></h3>
    </div>
    <div class="usp">
      <div class="usp-badge"><span><svg width="44" height="44" viewBox="0 0 44 44" fill="#fff"><circle cx="22" cy="16" r="12"/><circle cx="22" cy="16" r="6" fill="#3b3f4a"/><path d="M14 26l-4 14 6-3 4 5 2-14zM30 26l4 14-6-3-4 5-2-14z"/></svg></span></div>
      <div class="usp-stem"></div><div class="usp-dot"></div>
      <h3>1 year warranty</h3>
      <p>on the repair.</p>
    </div>
  </div>
</section>

<section class="process">
  <h2 class="section-title">Our<strong>Process</strong></h2>
  <div class="steps">
    <div class="step"><div class="step-art" role="img" aria-label="Cartoon engineer pointing at a phone to choose the device"></div><h3>Choose your device<br>and repair job</h3><p>Pick your brand, model and the part to fix.</p></div>
    <div class="step"><div class="step-art" role="img" aria-label="Cartoon engineer placing an order on a phone"></div><h3>Place the<br>order</h3><p>Confirm your request and send it to our team.</p></div>
    <div class="step"><div class="step-art" role="img" aria-label="Cartoon engineer answering a callback with a clock beside him"></div><h3>Get a callback within<br>the hour</h3><p>We ring back for a short intake and questions.</p></div>
    <div class="step"><div class="step-art" role="img" aria-label="Cartoon engineer holding a date and location sign"></div><h3>Set date and<br>location</h3><p>Pick a time and place that suits you best.</p></div>
    <div class="step"><div class="step-art" role="img" aria-label="Cartoon engineer walking with a toolbox to the customer"></div><h3>We will come<br>to you</h3><p>Our engineer arrives and repairs it while you wait.</p></div>
  </div>
</section>

<section class="help">
  <div class="help-photo" role="img" aria-label="Smiling woman with glasses talking on her phone"></div>
  <div class="help-copy">
    <p>You are not sure what the problem is with their device, and for this reason you are not sure what repair request they should order.</p>
    <h2>Dont Worry, You can always contact us whatever the problem you have.</h2>
    <a class="btn" href="#">Contact Us</a>
  </div>
</section>

<section class="testimonials">
  <h2 class="section-title">Clients’<strong>Testimonials</strong></h2>
  <div class="reviews">
    <div class="review">
      <div class="review-photo" role="img" aria-label="Portrait of client Mira Vance"></div>
      <blockquote>Donec turpis purus, dapibus sed turpis vel, condimentum ultricies sem leo magna condimentum nulla. ”<cite>- Mira Vance</cite></blockquote>
    </div>
    <div class="review">
      <div class="review-photo" role="img" aria-label="Portrait of client Tobin Hale"></div>
      <blockquote>Donec turpis purus, dapibus sed turpis vel, condimentum ultricies sem leo magna condimentum nulla. ”<cite>- Tobin Hale</cite></blockquote>
    </div>
  </div>
</section>

<section class="business">
  <div class="business-label">For<strong>Business</strong></div>
  <div class="business-body">
    <h2>The services we provide for corporate clients are-</h2>
    <ul>
      <li>In nec orci at diam sollicitudin mollis.</li>
      <li>Nunc venenatis ligula id purus varius, quis dapibus erat auctor.</li>
      <li>Suspendisse in diam vitae ex commodo commodo.</li>
    </ul>
  </div>
</section>

<footer class="site-footer">
  <div class="foot-col quick">
    <h4>Quick Links</h4>
    <ul><li>Home</li><li>Who We Are</li><li>What We Do</li><li>Our Process</li><li>Pricing</li><li>Testimonials</li><li>Our Clients</li><li>Contact Us</li></ul>
  </div>
  <div class="foot-col contact">
    <h4>Contact Information</h4>
    <ul>
      <li><svg width="14" height="18" viewBox="0 0 14 18"><path d="M7 0a7 7 0 0 0-7 7c0 5 7 11 7 11s7-6 7-11a7 7 0 0 0-7-7z" fill="#fff"/><circle cx="7" cy="7" r="2.5" fill="#121a20"/></svg><span>Lorem ipsum dolor sit amet<br>4820 310 5570<br>PO Box 7721 Harlow Bay 3390</span></li>
      <li><svg width="14" height="16" viewBox="0 0 14 16"><path d="M2 1l4 4-2 2c1 3 3 5 6 6l2-2 4 4-3 3C6 17-1 10 0 3z" fill="#fff"/></svg><span class="hot">Freecall 555 010 2468</span></li>
      <li><svg width="16" height="12" viewBox="0 0 16 12"><rect width="16" height="12" fill="#fff"/><path d="M0 0l8 6 8-6" fill="none" stroke="#121a20" stroke-width="1.5"/></svg><span>info@handsethaven.com</span></li>
    </ul>
  </div>
  <div class="foot-col newsletter">
    <h4>Newsletter Signup</h4>
    <p>Please enter your email address below to receive our FREE newsletter</p>
    <div class="news-field">Your Email ID</div>
    <span class="news-btn">Subscribe</span>
  </div>
  <div class="foot-col social">
    <h4>Follow Us</h4>
    <ul><li><i></i>Facefolio</li><li><i></i>Linkline</li><li><i></i>Chirper</li><li><i></i>Email</li></ul>
  </div>
</footer>
<div class="copyright">Copyright 2015@handsethaven.com. All Rights Are Reserved.</div>

</body>
</html>
```